New Business Card Design Project LORVANTI-Italy

we are LORVANTI-Italy
our company in the market for 3 years we are luxury cosmetic company and its about time for a facelift :)
i will like to have elegant luxurious and unique business card
that will give the person that get it a unique, luxurious and elegant impression
I'm VERY OPEN FOR NEW IDEAS , even duo i add a few files of things that i see on line and i like them

i add my logo as well
my website is LORVANTI.COM
(if you would like to see the main style that we have)

Target Market(s)

adult that have money :)

Industry/Entity Type

Business

Contact Information for Business Card

Name - Dario Lorvanti
Position - CEO and CO Founder
address - 4817 E Halvern
telephone - 555-384-1926
email - dario@lorvanti.com
fax - 555-384-1926
website - LORVANTI.COM

Colors
000000
959595
fbee3e
ffffff

Requirements
Must have
• big logo in GOLD color
• elegant look
• impressive
Nice to have
• not must but maybe classy pattern background
• not must but maybe emblem
• maybe clear plastic business card
Should not have
• colors
• images

```html
<!DOCTYPE html>
<html lang="en">
<head>
<meta charset="utf-8">
<title>LORVANTI Italy — Business Card</title>
<link href="https://fonts.googleapis.com/css2?family=Cinzel:wght@500&family=Roboto:wght@400;700&display=swap" rel="stylesheet">
<style>
  :root {
    --backdrop: #2f2925;
    --card: #141517;
    --card-edge: #0c0d0e;
    --gold: #d9a71c;
    --white: #ffffff;
    --grey: #959595;
    --faint: rgba(255,255,255,0.05);
  }
  * { margin: 0; padding: 0; box-sizing: border-box; }
  html, body { width: 1200px; height: 769px; overflow: hidden; }
  body {
    background: var(--backdrop);
    font-family: "Roboto", Arial, sans-serif;
    position: relative;
  }
  .card {
    position: absolute;
    width: 500px;
    height: 286px;
    background: var(--card);
    border-radius: 3px;
    box-shadow: 0 14px 30px rgba(0,0,0,0.55);
    overflow: hidden;
  }
  .card--back { left: 60px; top: 300px; }
  .card--front { left: 640px; top: 190px; box-shadow: 0 4px 0 var(--card-edge), 0 8px 0 #111, 0 18px 34px rgba(0,0,0,0.6); }

  .emblem-faint {
    position: absolute;
    left: 150px; top: 40px;
    width: 190px; height: 190px;
    border-radius: 50%;
    border: 10px solid var(--faint);
  }
  .identity {
    position: absolute;
    left: 190px; top: 70px;
    color: var(--white);
  }
  .identity__name {
    font-weight: 700;
    font-size: 24px;
    letter-spacing: 0.5px;
    padding-bottom: 4px;
    border-bottom: 2px solid var(--white);
  }
  .identity__title {
    font-size: 13px;
    margin-top: 5px;
    text-align: center;
    color: #e6e6e6;
  }
  .contacts {
    position: absolute;
    left: 0; right: 0; bottom: 34px;
    color: var(--white);
    font-size: 12.5px;
    text-align: center;
  }
  .contacts__row { display: flex; justify-content: center; gap: 12px; margin-top: 7px; }
  .contact { display: inline-flex; align-items: center; gap: 4px; }
  .contact svg { width: 12px; height: 12px; fill: var(--white); }

  .brand {
    position: absolute;
    inset: 0;
    display: flex;
    flex-direction: column;
    align-items: center;
    justify-content: center;
    color: var(--gold);
    font-family: "Cinzel", Georgia, serif;
    font-weight: 500;
  }
  .brand__mark {
    width: 72px; height: 72px;
    border-radius: 50%;
    background: var(--gold);
    margin-bottom: 16px;
  }
  .brand__name { font-size: 44px; letter-spacing: 1px; line-height: 1; }
  .brand__place { font-size: 14px; letter-spacing: 2px; margin-top: 8px; }
</style>
</head>
<body>

<section class="card card--back" aria-label="Business card, contact side">
  <div class="emblem-faint" role="img" aria-label="Faint brand emblem decoration"></div>
  <div class="identity">
    <div class="identity__name">DARIO LORVANTI</div>
    <div class="identity__title">CEO &amp; CO Founder</div>
  </div>
  <div class="contacts">
    <div class="contacts__row">
      <span class="contact"><svg viewBox="0 0 24 24"><path d="M6.6 10.8a15 15 0 0 0 6.6 6.6l2.2-2.2c.3-.3.7-.4 1-.2 1.1.4 2.3.6 3.6.6.6 0 1 .4 1 1V20c0 .6-.4 1-1 1A17 17 0 0 1 3 4c0-.6.4-1 1-1h3.5c.6 0 1 .4 1 1 0 1.3.2 2.5.6 3.6.1.3 0 .7-.2 1z"/></svg>555-384-1926</span>
      <span class="contact"><svg viewBox="0 0 24 24"><path d="M6 3h10l2 2v4H6zM3 10h18v8h-3v3H6v-3H3zm5 5v4h8v-4z"/></svg>555-384-1926</span>
      <span class="contact"><svg viewBox="0 0 24 24"><path d="M2 5h20v14H2zm2 2v.5l8 5 8-5V7z"/></svg>dario@lorvanti.com</span>
      <span class="contact"><svg viewBox="0 0 24 24"><path d="M12 2a10 10 0 1 0 0 20 10 10 0 0 0 0-20zm-1 17.9A8 8 0 0 1 4.1 11H7c.1 3 1.5 6.2 4 8.9zM7 9H4.3A8 8 0 0 1 11 4.1 13 13 0 0 0 7 9zm6 10.9c2.5-2.7 3.9-5.9 4-8.9h2.9a8 8 0 0 1-6.9 8.9zM17 9a13 13 0 0 0-4-4.9A8 8 0 0 1 19.7 9z"/></svg>LORVANTI.COM</span>
    </div>
    <div class="contacts__row">
      <span class="contact"><svg viewBox="0 0 24 24"><path d="M12 2a7 7 0 0 0-7 7c0 5 7 13 7 13s7-8 7-13a7 7 0 0 0-7-7zm0 9.5A2.5 2.5 0 1 1 12 6.5a2.5 2.5 0 0 1 0 5z"/></svg>4817 E Halvern</span>
    </div>
  </div>
</section>

<section class="card card--front" aria-label="Business card, brand side">
  <div class="brand">
    <div class="brand__mark"></div>
    <div class="brand__name">LORVANTI</div>
    <div class="brand__place">ITALY</div>
  </div>
</section>

</body>
</html>
```